Flyer Design Project For Kitchen Rendering Service

We need an A4 Page flyer designed for a new kitchen rendering service we are launching. Our target market is other kitchen designers/manufacturers. We want them to outsource the rendering of their kitchen designs to us. Many kitchen designers still hand draw kitchens using pen and paper. This makes it hard for the end client to visualise how their new kitchen will look. Utilising specialist rendering software we transform hand drawn sketches into photographic quality renders. We provide a few different prospective renders per order giving the customer and their client a complete visualisation of the room.
Here is a few links to examples we would like to showcase.
This is the sketch our client provided: https://www.filmora-vault.net/s/qw8rtbnzx41kplm/Kitchen%20Sketch.pdf
Below is some links to the end result that we provided our client:
https://www.filmora-vault.net/s/h207xqpbnd53wr8/Kitchen%20Brochure%20Sample%2001.jpg
https://www.filmora-vault.net/s/ktaw9pmfrbx2zcy/Kitchen%20Brochure%20Sample%2003.jpg
https://www.filmora-vault.net/s/wep48nbv692hdsa/Kitchen%20Brochure%20Sample%2002.jpg
https://www.filmora-vault.net/s/gmx3rtuzp07yfkc/Kitchen%20Brochure%20Sample%2004.jpg
https://www.filmora-vault.net/s/b6nqwypa2h85jte/Kitchen%20Brochure%20Sample%2005.jpg
Our website for more info is www.hazelgrid.com.au
We only require two things from our client.
1. A drawing of any kind explaining the design (can be sketch, cad, photo, etc).
2. A completed 'Render Information From' That can be downloaded from the photographic render page of our website. http://www.hazelgrid.com.au/#!photographic-rendering/vmtb
The final design should communicate how easy it is for a kitchen designer/manufacturer to transform their basic drawings/sketchs to a photograph quality renders and help them win more jobs and boost sales using our service.
Reason: We have extended the deadline by a few days to allow us to review and provide feedback to some last minute designs that have been submitted. Thank you to all the designers that have submitted designs. Stay tuned for our feedback
Target Market(s)
Our target market is other kitchen designers/manufacturers
Industry/Entity Type
Software
Look and feel
Each slider illustrates characteristics of the customer's brand and the style your logo design should communicate.

```html
<!DOCTYPE html>
<html lang="en">
<head>
<meta charset="utf-8">
<title>Hazelgrid – Kitchen Rendering Flyer</title>
<link href="https://fonts.googleapis.com/css2?family=Roboto:wght@300;400;700;900&display=swap" rel="stylesheet">
<style>
  :root{
    --brand-blue:#1f6b9c;
    --brand-blue-dark:#17557f;
    --accent-blue:#2f80c4;
    --heading-grey:#5a5a5a;
    --body-text:#2b2b2b;
    --page-top:#ffffff;
    --page-bottom:#d9e8f3;
    --white:#ffffff;
  }
  *{margin:0;padding:0;box-sizing:border-box}
  html,body{width:848px;height:1200px;overflow:hidden}
  body{font-family:"Roboto",Arial,sans-serif;color:var(--body-text)}
  .flyer{position:relative;width:848px;height:1200px;overflow:hidden;
    background:linear-gradient(180deg,var(--page-top) 40%,var(--page-bottom) 100%)}

  .hero-photo{position:absolute;left:0;top:0;width:848px;height:482px;
    background:linear-gradient(180deg,#e6e7e6 0%,#c9cbc8 45%,#8f918e 75%,#6d706c 100%)}
  .brand-tab{position:absolute;left:50px;top:0;width:168px;height:154px;background:var(--white);
    border-radius:0 0 18px 18px;box-shadow:0 2px 6px rgba(0,0,0,.25);
    display:flex;align-items:center;justify-content:center;gap:8px}
  .brand-tab .dot{width:16px;height:16px;border-radius:50%;background:var(--accent-blue)}
  .brand-tab .name{font-weight:700;font-size:24px;color:var(--brand-blue)}
  .hero-mark{position:absolute;right:16px;top:436px;font-weight:700;font-size:16px;color:var(--brand-blue)}

  .headline{position:absolute;left:68px;top:500px;color:var(--heading-grey)}
  .headline .just{position:absolute;left:0;top:20px;font-size:32px;font-weight:300;white-space:nowrap}
  .headline .steps{position:absolute;left:76px;top:0;font-size:76px;line-height:1;white-space:nowrap;font-weight:300;letter-spacing:-1px}
  .headline .steps b{font-weight:900}
  .headline .dream{position:absolute;left:0;top:96px;font-size:29px;font-weight:300;white-space:nowrap}
  .headline .kitchen{position:absolute;left:-2px;top:130px;font-size:80px;font-weight:900;line-height:1;letter-spacing:-1px}
  .headline .rendered{position:absolute;left:170px;top:210px;font-size:30px;font-weight:300;white-space:nowrap}

  .render-print{position:absolute;background:var(--white);padding:7px;box-shadow:2px 3px 8px rgba(0,0,0,.3)}
  .render-print .fill{width:100%;height:100%}
  .render-one{left:470px;top:420px;width:366px;height:220px;transform:rotate(7deg)}
  .render-one .fill{background:linear-gradient(160deg,#f2f2f2 0%,#dcdcdc 55%,#a98a64 80%,#cfc7bb 100%)}
  .render-two{left:486px;top:606px;width:352px;height:230px;transform:rotate(8deg)}
  .render-two .fill{background:linear-gradient(150deg,#eef0ef 0%,#4fa3b3 35%,#e9eae6 60%,#d6cfc4 100%)}

  .step{position:absolute;left:68px;width:400px}
  .step h2{font-weight:300;font-size:31px;color:var(--accent-blue);margin-bottom:8px}
  .step p{font-size:13px;line-height:18px;margin-bottom:10px}
  .step-one{top:782px}
  .step-two{top:952px}

  .difference{position:absolute;left:464px;top:888px;width:356px}
  .difference h3{display:inline-block;background:var(--accent-blue);color:var(--white);
    font-weight:400;font-size:18px;padding:3px 14px;width:236px;margin-bottom:14px}
  .difference p{font-size:13px;line-height:18px}

  .footer-band{position:absolute;left:0;top:1068px;width:848px;height:132px}
  .contact{position:absolute;left:64px;top:1092px;color:var(--white);font-weight:700;font-size:15px;line-height:26px}
  .contact .company{font-size:16px}
  .social{position:absolute;left:254px;top:1122px;display:flex;gap:14px}
  .social span{width:30px;height:30px;border-radius:6px;background:var(--accent-blue);border:2px solid var(--white)}
  .call{position:absolute;left:494px;top:1092px;font-size:35px;font-weight:400;color:var(--brand-blue)}
  .web{position:absolute;right:42px;top:1162px;font-size:22px;font-weight:700;color:var(--white)}
</style>
</head>
<body>
<div class="flyer">
  <div class="hero-photo" role="img" aria-label="Photographic render of a modern kitchen with marble island, bar stools and steel appliances"></div>
  <div class="brand-tab"><span class="dot"></span><span class="name">Hazelgrid</span></div>
  <div class="hero-mark">Hazelgrid</div>

  <div class="headline">
    <span class="just">Just</span>
    <span class="steps"><b>2</b>steps</span>
    <span class="dream">&amp; Get your Dream</span>
    <span class="kitchen">Kitchen</span>
    <span class="rendered">3D Rendered</span>
  </div>

  <div class="render-print render-one"><div class="fill" role="img" aria-label="Render of a white kitchen with timber benchtops and pendant lights"></div></div>
  <div class="render-print render-two"><div class="fill" role="img" aria-label="Render of a white L-shaped kitchen with a teal splashback"></div></div>

  <section class="step step-one">
    <h2>Step : 1</h2>
    <p>A drawing of any kind explaining the design (can be sketch, cad, photo, etc).</p>
    <p>Or A completed 'Render Information From' That can be downloaded from the photographic render page of our website. http://www.hazelgrid.com.au/<br>#!photographic-rendering/vmtb</p>
  </section>

  <section class="step step-two">
    <h2>Step : 2</h2>
    <p>Hazelgrid understands that your kitchen is the heart of your home. This is where families</p>
  </section>

  <section class="difference">
    <h3>The Hazelgrid Difference</h3>
    <p>Hazelgrid understands that your kitchen is the heart of your home. This is where families bond as they prepare an I need matter Hazelgrid understands that your kitchen is the heart of your home. This is where families bond as they prepare an I need matter</p>
  </section>

  <svg class="footer-band" viewBox="0 0 848 132" aria-hidden="true">
    <path d="M0 4 H408 C444 4 440 76 478 76 H848 V132 H0 Z" fill="var(--brand-blue)"/>
  </svg>
  <div class="contact">
    <div class="company">Hazelgrid Pty Ltd</div>
    <div>Merrowvale, NSW 2288</div>
    <div>info@hazelgrid.com.au</div>
  </div>
  <div class="social" aria-hidden="true"><span></span><span></span><span></span></div>
  <div class="call">Call : 0400 555 019</div>
  <div class="web">www.hazelgrid.com.au</div>
</div>
</body>
</html>
```